Simple Logo Design for Semi-Clear Plastic Frosted Card stock

Create a business card on frosted plastic. compliment existing logo elements with a tree trunk, roots, or seed at the lower half and the full logo both on the front.

Contact information will go on a solid portion of the back of this design since this card stock is semi-transparent.

It is important to consider this plastic card stock medium in your design. I found helpful tips and guides listed at vellaprint-sample.net: be careful to understand ink printed on plastic cards cannot have too much of a consistent print area or risks peeling and fine lines can easily scratch off.
Updates

2" x 3.5" 20PT Clear Plastic Business cards with Round corners Please get info or templates here: https://www.vellaprint-sample.net/product-detail/2-x-35-20pt-clear-plastic-business-cards-with-round-corners

Target Market(s)

Not for profit- religion

Industry/Entity Type

Business

Must include complementary elements to the existing logo

Font styles to use
Decorative

Colors
000000

Requirements
Must have
• Elements of community, nature and oneness. Such as: seed, roots, tree trunk, etc.
• Three lines of space on the back for Name, Title, Phone Number.
Nice to have
• I like a light use of decorative elements
Should not have
• No eyes, from faces or animals.

```html
<!DOCTYPE html>
<html lang="en">
<head>
<meta charset="utf-8">
<title>Meaningful Path – Business Card</title>
<link rel="stylesheet" href="https://fonts.googleapis.com/css2?family=Didact+Gothic&family=Libre+Baskerville:wght@700&family=Open+Sans:wght@300;400&display=swap">
<style>
  :root {
    --page-bg: #d9d9d7;
    --card-frost: #f1f1ef;
    --teal: #17594f;
    --leaf-green: #2f8c2c;
    --ink-dark: #2c2f30;
    --ink-light: #ffffff;
  }
  html, body {
    margin: 0;
    width: 1200px;
    height: 952px;
    overflow: hidden;
    background: var(--page-bg);
  }
  .card {
    position: absolute;
    left: 100px;
    top: 190px;
    width: 1000px;
    height: 571px;
    border-radius: 30px;
    overflow: hidden;
    background: var(--card-frost);
    box-shadow: 0 6px 18px rgba(0,0,0,0.12);
  }
  .card-bands {
    position: absolute;
    inset: 0;
  }
  .brand {
    position: absolute;
    left: 90px;
    top: 200px;
    display: flex;
    align-items: center;
    gap: 18px;
  }
  .brand-dot {
    width: 46px;
    height: 46px;
    border-radius: 50%;
    background: var(--teal);
  }
  .brand-name {
    font-family: "Didact Gothic", sans-serif;
    font-size: 58px;
    color: var(--ink-dark);
    letter-spacing: 1px;
    line-height: 1;
  }
  .brand-tagline {
    position: absolute;
    left: 155px;
    top: 272px;
    font-family: "Didact Gothic", sans-serif;
    font-size: 21px;
    letter-spacing: 1.5px;
    color: var(--ink-dark);
    white-space: nowrap;
  }
  .contact {
    position: absolute;
    right: 48px;
    top: 345px;
    text-align: right;
    color: var(--ink-light);
  }
  .contact-name {
    font-family: "Libre Baskerville", serif;
    font-weight: 700;
    font-size: 40px;
    margin: 0;
  }
  .contact-title {
    font-family: "Open Sans", sans-serif;
    font-weight: 300;
    font-size: 27px;
    margin: 4px 0 0;
  }
  .contact-phone {
    font-family: "Open Sans", sans-serif;
    font-weight: 300;
    font-size: 25px;
    margin: 34px 0 0;
    display: flex;
    align-items: center;
    justify-content: flex-end;
    gap: 18px;
  }
</style>
</head>
<body>
  <div class="card">
    <svg class="card-bands" width="1000" height="571" viewBox="0 0 1000 571">
      <polygon class="band-green" points="0,445 503,445 458,571 0,571" fill="var(--leaf-green)"/>
      <polygon class="band-teal" points="558,320 1000,320 1000,571 470,571" fill="var(--teal)"/>
    </svg>

    <div class="brand">
      <span class="brand-dot"></span>
      <span class="brand-name">MEANINGFUL PATH</span>
    </div>
    <div class="brand-tagline">LEARNING, FELLOWSHIP &amp; CALM</div>

    <div class="contact">
      <p class="contact-name">Owen Hartley</p>
      <p class="contact-title">Director</p>
      <p class="contact-phone">
        <span>0400 123 987</span>
        <svg class="phone-icon" width="22" height="30" viewBox="0 0 22 30" aria-hidden="true">
          <rect x="1" y="1" width="20" height="28" rx="3" fill="none" stroke="#fff" stroke-width="2"/>
          <rect x="5" y="5" width="12" height="10" fill="#fff"/>
          <rect x="5" y="18" width="12" height="7" fill="#fff" opacity="0.7"/>
        </svg>
      </p>
    </div>
  </div>
</body>
</html>
```